BRAVE MOTION Personal Training Website.

I am looking for a website design for Word Press URL I already have. I have it as 10 very simple pages. Once home page design is set we can use that look on all other pages. I have uploaded a word document that has an outline of what I am looking for. Please take the time to review this. I want to add this is for a WordPress site.

Target Market(s)

Women 25-55

Industry/Entity Type

Health And Wellness

Coding

Coded - Design and coding required

Number of Pages Required

5+ page

```html
<!DOCTYPE html>
<html lang="en">
<head>
<meta charset="utf-8">
<title>BRAVE MOTION – Personal Training</title>
<link href="https://fonts.googleapis.com/css2?family=Poppins:wght@400;500;600;700&family=Jost:wght@400;500;600&display=swap" rel="stylesheet">
<style>
:root{
  --red:#e8321e;
  --dark:#1b1b1b;
  --ink:#222;
  --grey:#6b6b6b;
  --light:#f4f4f4;
  --white:#fff;
}
*{box-sizing:border-box;margin:0;padding:0}
html,body{width:1200px;height:4276px;overflow:hidden}
body{font-family:"Jost",sans-serif;color:var(--ink);background:var(--white);position:relative}
.abs{position:absolute}
h2{font-family:"Poppins",sans-serif;font-weight:600;font-size:27px}
.red{color:var(--red)}
.btn{background:var(--red);color:var(--white);font-family:"Poppins",sans-serif;font-size:15px;font-weight:500;display:flex;align-items:center;justify-content:center;border:none}

/* header */
.hero{top:0;left:0;width:1200px;height:678px;background:linear-gradient(100deg,#8b95a3 0%,#c9ccd2 30%,#6e7480 55%,#2f333a 100%);overflow:hidden}
.hero-stripes{top:0;left:0}
.topnav{top:0;left:0;width:1200px;height:43px;background:rgba(20,20,20,.85);display:flex;align-items:center;padding-left:100px;gap:22px;font-size:15px;color:var(--white)}
.topnav .active{color:var(--red)}
.logo{top:62px;left:80px;display:flex;align-items:center;gap:10px;font-family:"Jost",sans-serif;font-weight:600;font-size:22px;color:var(--red)}
.logo i{width:40px;height:40px;border-radius:50%;background:var(--red);display:block}
.call{top:72px;left:738px;display:flex;align-items:center;gap:14px;color:var(--white);font-size:18px}
.call .num{color:var(--red);font-size:18px}
.call .ico{width:40px;height:40px;border-radius:50%;background:var(--red);display:flex;align-items:center;justify-content:center}
.social{top:82px;left:1100px;display:flex;gap:12px}
.social span{width:14px;height:14px;border-radius:50%;background:var(--white);display:block}
.tagline{top:325px;left:680px;font-family:"Poppins",sans-serif;font-weight:500;font-size:35px;line-height:1.35;color:var(--white)}

/* welcome */
.welcome-title{top:735px;left:80px}
.lead{top:795px;left:80px;width:560px;font-size:16px;font-weight:500;line-height:1.6}
.body-copy{top:890px;left:80px;width:560px;font-size:14px;line-height:1.75;color:var(--grey)}
.welcome-btn{top:1032px;left:78px;width:126px;height:42px}
.welcome-video{top:742px;left:705px;width:417px;height:333px;background:linear-gradient(135deg,#5a5d63,#9a9ea5 50%,#3c3f44)}
.play{width:66px;height:66px;border-radius:50%;background:var(--red);display:flex;align-items:center;justify-content:center;box-shadow:0 0 0 9px rgba(232,50,30,.3)}

/* certifications */
.certs{top:1134px;left:0;width:1200px;height:399px;background:var(--dark)}
.certs-photo{top:0;left:0;width:300px;height:399px;background:linear-gradient(90deg,#6a5b52 0%,#3a332f 70%,var(--dark) 100%)}
.certs-title{top:62px;left:250px}
.certs-text{top:122px;left:250px;width:640px;font-size:14px;line-height:1.75;color:#ddd}
.cert-row{top:211px;left:248px;display:flex;gap:12px}
.cert{width:165px;height:124px;background:var(--white);padding:14px 16px;display:flex;flex-direction:column;gap:8px}
.cert b{height:6px;background:#ccc;display:block}
.cert b.s{width:60%;margin:0 auto}
.cert em{margin-top:auto;width:44px;height:14px;background:#3c6cc1;display:block}

/* videos */
.vid-title{top:1590px;left:0;width:1200px;text-align:center}
.vid-main{top:1660px;left:340px;width:520px;height:330px;background:linear-gradient(135deg,#b5b8bd,#6f7379 60%,#3d4046)}
.thumbs{top:2025px;left:188px;display:flex;gap:12px}
.thumb{width:157px;height:105px;background:linear-gradient(135deg,#8d8478,#4b4641)}
.arrow-btn{width:34px;height:34px;border-radius:50%;background:var(--white);box-shadow:0 0 6px rgba(0,0,0,.15);display:flex;align-items:center;justify-content:center}

/* testimonial */
.testi{top:2189px;left:0;width:1200px;height:490px;background:linear-gradient(180deg,#2c2a2a,#403c3a 50%,#262424)}
.testi-title{top:60px;left:0;width:1200px;text-align:center;color:var(--white);font-size:26px}
.testi-box{top:127px;left:288px;width:624px;height:180px;background:rgba(255,255,255,.18);padding:30px 70px;text-align:center;color:var(--white);font-size:14px;line-height:1.8}
.testi-name{top:305px;left:0;width:1200px;text-align:center;color:var(--red);font-family:"Poppins",sans-serif;font-size:14px;font-weight:500}
.sq{width:30px;height:30px;display:flex;align-items:center;justify-content:center}
.avatar{top:340px;left:556px;width:88px;height:88px;border-radius:50%;background:linear-gradient(#d9c2b4,#a88a7a);border:4px solid var(--white)}

/* blog */
.blog-title{top:2735px;left:0;width:1200px;text-align:center}
.post{top:2813px;width:322px}
.post-img{height:200px;background:linear-gradient(135deg,#cfd3d8,#7d838b)}
.post h3{font-family:"Poppins",sans-serif;font-size:15px;font-weight:600;margin-top:22px}
.post-meta{display:flex;justify-content:space-between;margin-top:12px;font-size:13px;color:var(--grey)}
.post-meta .more{color:var(--red);font-weight:500}

/* contact */
.contact{top:3149px;left:0;width:1200px;height:491px;background:linear-gradient(160deg,#2a2a2c,#4a4446 50%,#1e1e20)}
.contact-title{top:60px;left:0;width:1200px;text-align:center;color:var(--white);font-size:26px}
.contact-text{top:118px;left:280px;width:640px;text-align:center;color:#ddd;font-size:14px;line-height:1.75}
.field{color:#ccc;font-size:13px;border-bottom:1px solid rgba(255,255,255,.35);padding-bottom:10px}
.contact-btn{top:385px;left:537px;width:126px;height:42px}

/* subscribe */
.sub-title{top:3690px;left:0;width:1200px;text-align:center;color:var(--red)}
.sub-text{top:3763px;left:0;width:1200px;text-align:center;color:var(--grey);font-size:13px}
.sub-field{font-size:13px;color:var(--grey);border-bottom:1px solid #bbb;padding-bottom:10px}
.sub-btn{top:3826px;left:870px;width:125px;height:42px}

/* footer */
.footer{top:3927px;left:0;width:1200px;height:349px;background:#0f0f0f;color:#e8e8e8;font-size:14px}
.footer h4{font-family:"Poppins",sans-serif;font-size:16px;font-weight:500;color:var(--red)}
.footer ul{list-style:none;line-height:1.95}
.contact-line{display:flex;gap:16px;align-items:flex-start;line-height:1.7}
.foot-logo{top:60px;left:890px}
.foot-about{top:140px;left:815px;width:300px;text-align:center;line-height:1.7}
.foot-rule{top:282px;left:80px;width:1040px;height:1px;background:#333}
.copyright{top:305px;left:0;width:1200px;text-align:center;color:var(--red);font-size:13px}
</style>
</head>
<body>

<header class="hero abs" role="img" aria-label="Photo of a smiling woman training in a gym with another athlete behind her">
  <svg class="hero-stripes abs" width="1200" height="678" viewBox="0 0 1200 678" aria-hidden="true">
    <polygon points="395,0 430,0 965,678 930,678" fill="#e8321e" opacity=".9"/>
    <polygon points="520,0 545,0 1060,678 1035,678" fill="#e8321e" opacity=".55"/>
  </svg>
</header>

<nav class="topnav abs">
  <span>Certifications</span><span>Bio</span><span>Blog</span><span class="active">Videos</span><span>Online Training</span><span>Functional Movement Screening</span><span>Nutrition Section</span><span>Merchandise</span><span>Contact Us</span>
</nav>
<div class="logo abs"><i></i>BRAVE MOTION</div>
<div class="call abs">Call on
  <span class="ico"><svg width="18" height="18" viewBox="0 0 24 24"><path d="M6.6 10.8a15 15 0 0 0 6.6 6.6l2.2-2.2c.3-.3.7-.4 1-.2 1.1.4 2.3.6 3.6.6.6 0 1 .4 1 1V20c0 .6-.4 1-1 1A17 17 0 0 1 3 4c0-.6.4-1 1-1h3.5c.6 0 1 .4 1 1 0 1.3.2 2.5.6 3.6.1.3 0 .7-.2 1z" fill="#fff"/></svg></span>
  <span class="num">123 456 7890</span>
</div>
<div class="social abs" aria-label="Social links"><span></span><span></span></div>
<p class="tagline abs">If it doesn't Challenge you,<br>it won't Change you.</p>

<!-- welcome -->
<h2 class="welcome-title abs"><span class="red">Welcome To</span> <span class="red">BRAVE MOTION</span></h2>
<p class="lead abs">Lorem Ipsum is simply dummy text of the printing and typesetting industry. Lorem Ipsum has been the industry's standard dummy text ever since the 1500s.</p>
<p class="body-copy abs">Lorem Ipsum is simply dummy text of the printing and typesetting industry. Lorem Ipsum has been the industry's standard dummy text ever since the 1500s, when an unknown printer took a galley of type and scrambled it to make a type electronic typesetting, remaining essentially unchanged.</p>
<div class="btn welcome-btn abs">Learn More</div>
<div class="welcome-video abs" role="img" aria-label="Video still of a man and woman doing squats in a gym"></div>
<div class="play abs" style="top:874px;left:672px"><svg width="20" height="20" viewBox="0 0 20 20"><circle cx="10" cy="10" r="8" fill="none" stroke="#fff" stroke-width="1.6"/><path d="M8 6l5 4-5 4z" fill="#fff"/></svg></div>

<!-- certifications -->
<section class="certs abs">
  <div class="certs-photo abs" role="img" aria-label="Photo of a fit woman in sports wear"></div>
  <h2 class="certs-title abs red">Certifications</h2>
  <p class="certs-text abs">Lorem Ipsum is simply dummy text of the printing and typesetting industry. Lorem Ipsum has been the industry's standard dummy text ever since the 1500s.</p>
  <div class="cert-row abs">
    <div class="cert"><b class="s"></b><b></b><b class="s"></b><em></em></div>
    <div class="cert"><b class="s"></b><b></b><b class="s"></b><em></em></div>
    <div class="cert"><b class="s"></b><b></b><b class="s"></b><em></em></div>
    <div class="cert"><b class="s"></b><b></b><b class="s"></b><em></em></div>
    <div class="cert"><b class="s"></b><b></b><b class="s"></b><em></em></div>
  </div>
</section>

<!-- videos -->
<h2 class="vid-title abs"><span class="red">BRAVE MOTION</span> Videos</h2>
<div class="vid-main abs" role="img" aria-label="Video still of a woman and man exercising with dumbbells"></div>
<div class="play abs" style="top:1792px;left:567px"><svg width="20" height="20" viewBox="0 0 20 20"><path d="M6 4l10 6-10 6z" fill="#fff"/></svg></div>
<div class="thumbs abs">
  <div class="thumb" role="img" aria-label="Video thumbnail: group workout"></div>
  <div class="thumb" role="img" aria-label="Video thumbnail: cycling class"></div>
  <div class="thumb" role="img" aria-label="Video thumbnail: stretching"></div>
  <div class="thumb" role="img" aria-label="Video thumbnail: weights"></div>
  <div class="thumb" role="img" aria-label="Video thumbnail: gym floor"></div>
</div>
<div class="arrow-btn abs" style="top:2061px;left:125px"><svg width="10" height="10" viewBox="0 0 10 10"><path d="M7 1L3 5l4 4" fill="none" stroke="#bbb" stroke-width="1.5"/></svg></div>
<div class="arrow-btn abs" style="top:2061px;left:1040px"><svg width="10" height="10" viewBox="0 0 10 10"><path d="M3 1l4 4-4 4" fill="none" stroke="#e8321e" stroke-width="1.5"/></svg></div>

<!-- testimonial -->
<section class="testi abs" role="img" aria-label="Dim photo of a group fitness class">
  <h2 class="testi-title abs"><span class="red">Client</span> Testimonial</h2>
  <div class="testi-box abs">I wasn't sure if Maren was interested in training my then 11-year-old daughter, but after talking with her she was 100% committed to what we wanted to accomplish with our daughter. After their first intro session together, my daughter was excited and....</div>
  <div class="sq abs" style="top:242px;left:272px;background:#fff"><svg width="10" height="10" viewBox="0 0 10 10"><path d="M7 1L2 5l5 4z" fill="#888"/></svg></div>
  <div class="sq abs" style="top:242px;left:898px;background:var(--red)"><svg width="10" height="10" viewBox="0 0 10 10"><path d="M3 1l5 4-5 4z" fill="#fff"/></svg></div>
  <p class="testi-name abs">Jessica Hale</p>
  <div class="avatar abs" role="img" aria-label="Client portrait"></div>
</section>

<!-- blog -->
<h2 class="blog-title abs red">Latest Blog</h2>
<article class="post abs" style="left:80px">
  <div class="post-img" role="img" aria-label="Photo of women on elliptical trainers"></div>
  <h3>Lorem Ipsum is typesetting industry.</h3>
  <div class="post-meta"><span>🗨 Comments</span><span class="more">Learn More →</span></div>
</article>
<article class="post abs" style="left:440px">
  <div class="post-img" role="img" aria-label="Photo of a woman on a spin bike"></div>
  <h3>Lorem Ipsum is typesetting industry.</h3>
  <div class="post-meta"><span>🗨 Comments</span><span class="more">Learn More →</span></div>
</article>
<article class="post abs" style="left:800px">
  <div class="post-img" role="img" aria-label="Photo of a group doing weight plate exercises"></div>
  <h3>Lorem Ipsum is typesetting industry.</h3>
  <div class="post-meta"><span>🗨 Comments</span><span class="more">Learn More →</span></div>
</article>

<!-- contact -->
<section class="contact abs" role="img" aria-label="Dim photo of a woman exercising on a treadmill">
  <h2 class="contact-title abs"><span class="red">Contact</span> Us</h2>
  <p class="contact-text abs">Lorem Ipsum is simply dummy text of the printing and typesetting industry. Lorem Ipsum has been the industry's standard dummy text ever since the 1500s.</p>
  <div class="field abs" style="top:218px;left:300px;width:290px">Name*</div>
  <div class="field abs" style="top:218px;left:615px;width:290px">E-mail*</div>
  <div class="field abs" style="top:272px;left:300px;width:290px">Phone*</div>
  <div class="field abs" style="top:272px;left:615px;width:290px">Subject</div>
  <div class="field abs" style="top:326px;left:300px;width:605px;padding-bottom:30px">Message</div>
  <div class="btn contact-btn abs">Learn More</div>
</section>

<!-- subscribe -->
<h2 class="sub-title abs">Subscribe Us!</h2>
<p class="sub-text abs">For latest news or updates subscribe our newsletter</p>
<div class="sub-field abs" style="top:3836px;left:205px;width:300px">Name*</div>
<div class="sub-field abs" style="top:3836px;left:540px;width:310px">E-mail*</div>
<div class="btn sub-btn abs">Subscribe</div>

<!-- footer -->
<footer class="footer abs">
  <h4 class="abs" style="top:48px;left:80px">Site Map</h4>
  <ul class="abs" style="top:85px;left:80px">
    <li>Certifications</li><li>Bio</li><li>Blog</li><li>Videos</li><li>Online Training</li><li>Functional Movement Screening</li>
  </ul>
  <ul class="abs" style="top:85px;left:263px">
    <li>Nutrition Section</li><li>Merchandise</li><li>Contact Us</li>
  </ul>
  <h4 class="abs" style="top:48px;left:440px">Get In Touch</h4>
  <div class="abs" style="top:90px;left:440px;display:flex;flex-direction:column;gap:20px">
    <div class="contact-line"><svg width="14" height="18" viewBox="0 0 14 18"><path d="M7 0a7 7 0 0 0-7 7c0 5 7 11 7 11s7-6 7-11a7 7 0 0 0-7-7zm0 10a3 3 0 1 1 0-6 3 3 0 0 1 0 6z" fill="#e8321e"/></svg><span>123, Lorem ipsum is simply<br>dummy text</span></div>
    <div class="contact-line"><svg width="16" height="16" viewBox="0 0 24 24"><path d="M6.6 10.8a15 15 0 0 0 6.6 6.6l2.2-2.2c.3-.3.7-.4 1-.2 1.1.4 2.3.6 3.6.6.6 0 1 .4 1 1V20c0 .6-.4 1-1 1A17 17 0 0 1 3 4c0-.6.4-1 1-1h3.5c.6 0 1 .4 1 1 0 1.3.2 2.5.6 3.6.1.3 0 .7-.2 1z" fill="#e8321e"/></svg><span>123 456 7890</span></div>
    <div class="contact-line"><svg width="16" height="14" viewBox="0 0 16 12"><rect width="16" height="12" rx="1" fill="#e8321e"/><path d="M1 1l7 6 7-6" fill="none" stroke="#0f0f0f" stroke-width="1.3"/></svg><span>info@bravemotion.com</span></div>
  </div>
  <div class="logo foot-logo abs" style="top:58px;left:890px"><i></i>BRAVE MOTION</div>
  <p class="foot-about abs">Lorem Ipsum is simply dummy text of the printing and typesetting industry. Lorem Ipsum has been the industry's standard dummy text ever since the 1500s.</p>
  <div class="foot-rule abs"></div>
  <p class="copyright abs">© BRAVE MOTION - 2016. All Rights Reserved.</p>
</footer>

</body>
</html>
```